BrivoNest Learning App for Children with Dyslexia

Project Description:

We are seeking a talented UI/UX designer to create engaging and intuitive designs for Brivonest, an innovative educational app designed to help children learn letters and words through a multisensory learning approach. The app aims to be particularly helpful for children with dyslexia, providing a supportive and interactive learning environment.

Key App Features & Design Requirements:

Account Creation Screen: Design a welcoming and straightforward sign-up page that allows users to register with their email or continue with Quarnix. The design should be clean, focusing on user-friendliness and accessibility, adhering to our terms of service and privacy policy.

Main Screen Design: The main screen should allocate at least 4/6 of its height to the interactive drawing area. It needs to display word prompts in both correct and scrambled orders and include options to "Show all Words," "Play all words," and a search function. The interface should be vibrant, engaging, and easy to navigate for children.

Profile Section: Create a user-friendly profile page that allows users to edit their profile image, name, username, email, links, and bio. The design should be clean and encourage user engagement.

BrivoTally Page: This section will display the user's learning progress, including rankings, a learning curve, and recently learned words. It should visually represent progress in a motivating and understandable way, suitable for a younger audience.

Visual and Auditory Feedback Implementation: Incorporate elements that support visual and auditory feedback, using dyslexia-friendly formats. This includes choosing appropriate colors, fonts, and auditory cues.

Accessibility and Customization Settings: Designs should include settings for adjusting visual contrast, font size, and the word list to accommodate individual preferences and needs.

Feel free to add more interactions and/or pages.

Design preferences:

Color Scheme: Use a bright, inviting color palette that stimulates learning and engagement without overwhelming the users.
Font Selection: Opt for fonts that are readable and accessible, particularly for users with dyslexia.
Icons and Graphics: Design custom icons and graphics that are cohesive with the app's theme and purpose. Illustrations should be simple, relatable, and supportive of the learning process.

Target Market(s)

Educational

Industry/Entity Type

Educational

Colors
0054AA
0677BA
7BADD7
CADEEF
E8F1F8
0094D4
00A9DD
6FCCEA
C7EBF8
E9F6FB

Requirements
Must have
• Educational app, a writing area, scoring and account management
Nice to have
• Statistics, Ranking Page, Settings and some nice visual features

```html
<!DOCTYPE html>
<html lang="en">
<head>
<meta charset="utf-8">
<title>Brivonest – App Screens</title>
<link href="https://fonts.googleapis.com/css2?family=Montserrat:wght@400;500;600;700&family=Roboto:wght@400;500;700&display=swap" rel="stylesheet">
<style>
  :root{
    --brand:#0054AA;
    --brand-mid:#0677BA;
    --sky:#7BADD7;
    --pale:#CADEEF;
    --mist:#E8F1F8;
    --ink:#111111;
    --text:#222222;
    --line:#4a4a4a;
    --canvas:#DDDDDD;
    --white:#FFFFFF;
  }
  *{box-sizing:border-box;margin:0;padding:0}
  html,body{width:1200px;height:807px;overflow:hidden;background:var(--white)}
  body{position:relative;font-family:"Montserrat",sans-serif;color:var(--text)}

  .screen{position:absolute;top:21px;width:350px;height:756px;background:var(--white);overflow:hidden;
    box-shadow:0 1px 6px rgba(0,0,0,.12)}
  .screen--signup{left:31px}
  .screen--main{left:420px}
  .screen--profile{left:809px}

  .status-bar{position:absolute;left:0;top:0;width:100%;height:29px;background:var(--brand);z-index:3;
    display:flex;align-items:center;justify-content:space-between;padding:0 9px 0 10px;color:var(--white);
    font:600 10px "Montserrat",sans-serif}
  .status-icons{display:flex;gap:6px;align-items:center}
  .home-indicator{position:absolute;left:101px;top:740px;width:144px;height:2px;background:var(--ink)}

  /* Sign up */
  .signup-hero{position:absolute;left:0;top:0;width:350px;height:380px}
  .brand-title{position:absolute;left:0;width:100%;top:80px;text-align:center;color:var(--white);
    font:700 39px "Roboto",sans-serif;letter-spacing:.5px}
  .brand-tagline{position:absolute;left:0;width:100%;top:125px;text-align:center;color:var(--white);
    font:400 15px "Roboto",sans-serif}
  .signup-card{position:absolute;left:22px;top:198px;width:302px;height:421px;background:var(--white);
    border:1px solid var(--brand);border-radius:8px;box-shadow:0 2px 8px rgba(0,0,0,.08)}
  .card-title{position:absolute;top:32px;width:100%;text-align:center;font:700 19px "Roboto",sans-serif;color:var(--ink)}
  .card-sub{position:absolute;top:70px;width:100%;text-align:center;font-size:12px;color:var(--ink)}
  .email-field{position:absolute;left:19px;top:119px;width:265px;height:29px;border-bottom:2px solid var(--brand);
    font-size:12px;color:#555;padding-left:4px}
  .btn{position:absolute;border-radius:20px;display:flex;align-items:center;justify-content:center;
    font:600 13.5px "Montserrat",sans-serif}
  .btn--primary{background:var(--brand);color:var(--white)}
  .btn--email{left:23px;top:172px;width:258px;height:39px}
  .divider{position:absolute;left:9px;top:243px;width:284px;display:flex;align-items:center;gap:6px;font-size:12px;color:#333}
  .divider::before,.divider::after{content:"";flex:1;height:1px;background:#555}
  .btn--social{left:23px;top:287px;width:258px;height:38px;background:var(--pale);color:var(--ink);gap:8px}
  .social-dot{width:16px;height:16px;border-radius:50%;background:var(--brand)}
  .terms{position:absolute;top:356px;width:100%;text-align:center;font-size:11.5px;line-height:26px;color:#333}
  .terms strong{font-weight:600;color:var(--ink)}

  /* Main */
  .status-curve{position:absolute;left:0;top:28px;z-index:2}
  .menu-icon{position:absolute;left:17px;top:56px}
  .screen-title{position:absolute;left:0;width:100%;top:54px;text-align:center;font:700 20px "Roboto",sans-serif;color:var(--ink)}
  .points{position:absolute;right:12px;top:56px;font:700 14.5px "Roboto",sans-serif;color:var(--ink)}
  .drawing-area{position:absolute;left:6px;top:99px;width:338px;height:274px;background:var(--canvas)}
  .tool-button{position:absolute;left:273px;top:305px;width:64px;height:59px;background:var(--brand);
    display:flex;align-items:center;justify-content:center}
  .mode-toggle{position:absolute;left:11px;top:394px;width:327px;height:42px;border:1px solid #333;border-radius:21px;
    font:700 12.5px "Roboto",sans-serif;color:var(--ink)}
  .mode-toggle span{position:absolute;top:0;height:100%;display:flex;align-items:center;justify-content:center}
  .mode-show{left:0;width:160px}
  .mode-play{left:160px;top:2px!important;height:36px!important;width:163px;background:var(--brand);color:var(--white);border-radius:19px}
  .word-tile{position:absolute;width:100px;height:85px;border-radius:14px;background:var(--white);
    box-shadow:0 1px 6px rgba(0,0,0,.14);display:flex;align-items:center;justify-content:center;text-align:center;
    font:700 20px/26px "Montserrat",sans-serif;color:var(--ink)}
  .btn--results{left:44px;top:674px;width:258px;height:39px}

  /* Profile */
  .cover-art{position:absolute;left:0;top:29px;width:350px;height:140px;
    background:linear-gradient(100deg,#f4e6c8 0%,#f4e6c8 24%,#2d6fb3 32%,#7a3fa0 48%,#e0457b 62%,#f29a3b 76%,#d23f86 88%,#3a7dc4 100%)}
  .profile-sheet{position:absolute;left:0;top:139px;width:350px;height:620px;background:var(--white);border-radius:42px 42px 0 0}
  .back-link{position:absolute;left:9px;top:58px;display:flex;align-items:center;gap:4px;font:600 9px "Montserrat",sans-serif;color:var(--ink);z-index:2}
  .avatar{position:absolute;left:114px;top:85px;width:120px;height:120px;border-radius:50%;border:2px solid var(--brand);
    background:radial-gradient(circle at 50% 40%,#c9b7a6 0%,#8a7565 55%,#d9d9d9 100%)}
  .profile-title{position:absolute;top:231px;width:100%;text-align:center;font:700 19.5px "Roboto",sans-serif;color:var(--ink)}
  .field{position:absolute;left:9px;width:328px;border:1px solid var(--line);border-radius:21px;padding:0}
  .field legend{margin-left:22px;padding:0 6px;font:500 14.5px/18px "Montserrat",sans-serif;color:var(--brand)}
  .field-row{height:33px;padding:0 16px 6px 20px;display:flex;align-items:center;justify-content:space-between;font-size:13.5px;color:var(--ink)}
  .field--links .link-list{list-style:none;padding:4px 0 8px 20px;font-size:13.5px;line-height:25.5px;color:var(--ink)}
  .link-list .add-link{color:#888}
</style>
</head>
<body>

<!-- Sign up screen -->
<section class="screen screen--signup" aria-label="Create account screen">
  <div class="status-bar"><span>9.45</span>
    <span class="status-icons">
      <svg width="20" height="10" viewBox="0 0 20 10"><rect x="0" y="7" width="3" height="3" fill="#fff"/><rect x="5" y="5" width="3" height="5" fill="#fff"/><rect x="10" y="3" width="3" height="7" fill="#fff"/><rect x="15" y="0" width="3" height="10" fill="#fff"/></svg>
      <svg width="16" height="12" viewBox="0 0 16 12"><path d="M1 4a10 10 0 0 1 14 0M3.5 6.5a6.5 6.5 0 0 1 9 0M6 9a3 3 0 0 1 4 0" stroke="#fff" stroke-width="1.8" fill="none"/><circle cx="8" cy="11" r="1" fill="#fff"/></svg>
      <svg width="22" height="11" viewBox="0 0 22 11"><rect x="1" y="1" width="18" height="9" rx="2" stroke="#fff" fill="none"/><rect x="20" y="4" width="1.5" height="3" fill="#fff"/><rect x="2.5" y="2.5" width="4" height="6" fill="#fff"/></svg>
    </span>
  </div>
  <svg class="signup-hero" viewBox="0 0 350 380" preserveAspectRatio="none" aria-hidden="true">
    <path d="M0 0H350V342Q175 300 0 342Z" fill="var(--brand)"/>
  </svg>
  <h1 class="brand-title">Brivonest</h1>
  <p class="brand-tagline">Learn letters and words</p>

  <div class="signup-card">
    <h2 class="card-title">Create an Account</h2>
    <p class="card-sub">Enter your email to sign up for this app</p>
    <div class="email-field">Email@domain.com</div>
    <div class="btn btn--primary btn--email">Sign up with email</div>
    <div class="divider">Or Continue With</div>
    <div class="btn btn--social"><span class="social-dot"></span>Quarnix</div>
    <p class="terms">By clicking continue, you agree to our<br><strong>Terms of Service</strong> and <strong>Privacy Policy</strong></p>
  </div>
  <div class="home-indicator"></div>
</section>

<!-- Main screen -->
<section class="screen screen--main" aria-label="Main screen">
  <div class="status-bar"><span>9.45</span>
    <span class="status-icons">
      <svg width="20" height="10" viewBox="0 0 20 10"><rect x="0" y="7" width="3" height="3" fill="#fff"/><rect x="5" y="5" width="3" height="5" fill="#fff"/><rect x="10" y="3" width="3" height="7" fill="#fff"/><rect x="15" y="0" width="3" height="10" fill="#fff"/></svg>
      <svg width="16" height="12" viewBox="0 0 16 12"><path d="M1 4a10 10 0 0 1 14 0M3.5 6.5a6.5 6.5 0 0 1 9 0M6 9a3 3 0 0 1 4 0" stroke="#fff" stroke-width="1.8" fill="none"/><circle cx="8" cy="11" r="1" fill="#fff"/></svg>
      <svg width="22" height="11" viewBox="0 0 22 11"><rect x="1" y="1" width="18" height="9" rx="2" stroke="#fff" fill="none"/><rect x="20" y="4" width="1.5" height="3" fill="#fff"/><rect x="2.5" y="2.5" width="4" height="6" fill="#fff"/></svg>
    </span>
  </div>
  <svg class="status-curve" width="350" height="5" viewBox="0 0 350 5" aria-hidden="true"><path d="M0 0H350V1Q175 6 0 1Z" fill="var(--brand)"/></svg>
  <svg class="menu-icon" width="30" height="24" viewBox="0 0 30 24" aria-label="Menu"><path d="M0 2H30M0 12H30M0 22H30" stroke="var(--brand)" stroke-width="3"/></svg>
  <h2 class="screen-title">Main Screen</h2>
  <span class="points">16 Points</span>

  <div class="drawing-area" aria-label="Drawing area"></div>
  <div class="tool-button" aria-label="Drawing tools">
    <svg width="40" height="44" viewBox="0 0 40 44">
      <path d="M18 6C8 6 2 13 2 22s6 16 15 16c4 0 5-3 3-6s0-6 4-6h4c3 0 4-3 4-6C32 11 26 6 18 6Z" fill="#fff"/>
      <circle cx="9" cy="20" r="2.6" fill="var(--brand)"/><circle cx="14" cy="13" r="2.6" fill="var(--brand)"/>
      <circle cx="22" cy="13" r="2.6" fill="var(--brand)"/><circle cx="10" cy="29" r="2.6" fill="var(--brand)"/>
      <rect x="34" y="4" width="3" height="36" rx="1.5" fill="#fff"/>
    </svg>
  </div>

  <div class="mode-toggle">
    <span class="mode-show">Show all Words</span>
    <span class="mode-play">Play All Words</span>
  </div>

  <div class="word-tile" style="left:16px;top:456px">Word<br>1</div>
  <div class="word-tile" style="left:124px;top:456px">Word<br>2</div>
  <div class="word-tile" style="left:233px;top:456px">Word<br>3</div>
  <div class="word-tile" style="left:16px;top:560px">Word<br>4</div>
  <div class="word-tile" style="left:124px;top:560px">Word<br>5</div>
  <div class="word-tile" style="left:233px;top:560px;font-size:14px">••••</div>

  <div class="btn btn--primary btn--results">Show Me The Results</div>
  <div class="home-indicator"></div>
</section>

<!-- Profile screen -->
<section class="screen screen--profile" aria-label="Edit profile screen">
  <div class="status-bar"><span>9.45</span>
    <span class="status-icons">
      <svg width="20" height="10" viewBox="0 0 20 10"><rect x="0" y="7" width="3" height="3" fill="#fff"/><rect x="5" y="5" width="3" height="5" fill="#fff"/><rect x="10" y="3" width="3" height="7" fill="#fff"/><rect x="15" y="0" width="3" height="10" fill="#fff"/></svg>
      <svg width="16" height="12" viewBox="0 0 16 12"><path d="M1 4a10 10 0 0 1 14 0M3.5 6.5a6.5 6.5 0 0 1 9 0M6 9a3 3 0 0 1 4 0" stroke="#fff" stroke-width="1.8" fill="none"/><circle cx="8" cy="11" r="1" fill="#fff"/></svg>
      <svg width="22" height="11" viewBox="0 0 22 11"><rect x="1" y="1" width="18" height="9" rx="2" stroke="#fff" fill="none"/><rect x="20" y="4" width="1.5" height="3" fill="#fff"/><rect x="2.5" y="2.5" width="4" height="6" fill="#fff"/></svg>
    </span>
  </div>
  <div class="cover-art" role="img" aria-label="Colourful illustrated cover with profiles of faces in blue, pink and orange"></div>
  <div class="back-link">
    <svg width="10" height="16" viewBox="0 0 10 16"><path d="M8 1L2 8l6 7" stroke="var(--ink)" stroke-width="2" fill="none"/></svg>Back
  </div>
  <div class="profile-sheet"></div>
  <div class="avatar" role="img" aria-label="User profile photo"></div>
  <h2 class="profile-title">Edit Profile Image</h2>

  <fieldset class="field" style="top:279px"><legend>Name</legend>
    <div class="field-row"><span>Nora Vale</span><svg width="10" height="18" viewBox="0 0 10 18"><path d="M1 1l8 8-8 8" stroke="#444" stroke-width="1.6" fill="none"/></svg></div>
  </fieldset>
  <fieldset class="field" style="top:353px"><legend>Username</legend>
    <div class="field-row"><span>@username</span><svg width="10" height="18" viewBox="0 0 10 18"><path d="M1 1l8 8-8 8" stroke="#444" stroke-width="1.6" fill="none"/></svg></div>
  </fieldset>
  <fieldset class="field" style="top:428px"><legend>Email</legend>
    <div class="field-row"><span>name@domain.com</span><svg width="10" height="18" viewBox="0 0 10 18"><path d="M1 1l8 8-8 8" stroke="#444" stroke-width="1.6" fill="none"/></svg></div>
  </fieldset>
  <fieldset class="field field--links" style="top:501px"><legend>Links</legend>
    <ul class="link-list">
      <li>website.net</li><li>mylink.net</li><li>yourlink.net</li><li class="add-link">+ Add link</li>
    </ul>
  </fieldset>
  <fieldset class="field" style="top:656px"><legend>Bio</legend>
    <div class="field-row"><span>A description of this user.</span><svg width="10" height="18" viewBox="0 0 10 18"><path d="M1 1l8 8-8 8" stroke="#444" stroke-width="1.6" fill="none"/></svg></div>
  </fieldset>
  <div class="home-indicator"></div>
</section>

</body>
</html>
```